Website design for an Italian restaurant in Amsterdam

I need a design for a client of mine. It is for Teatro Lucerna, an Italian restaurant in Amsterdam.
We are going for a clean, modern look but we also need to realise an authentic feel.
The restaurant is located in an old movie theatre, that is where the name Teatro Lucerna comes from.
Industry/Entity Type
Italian Restaurant
Number of Pages Required
1 page
Font styles to use
Sans Serif
Colors
Designer to choose colors to be used in the design.

```html
<!DOCTYPE html>
<html lang="en">
<head>
<meta charset="utf-8">
<title>Teatro Lucerna — Italian Restaurant Amsterdam</title>
<link href="https://fonts.googleapis.com/css2?family=Montserrat:wght@400;500;600;700;800&display=swap" rel="stylesheet">
<style>
:root{
  --accent:#b23a5a;
  --ink:#111111;
  --night:#0b0b0b;
  --paper:#ffffff;
  --mist:#ececec;
  --grey:#e1e1e1;
  --line:#c9c9c9;
  --muted:#8a8a8a;
  --green:#2e8b3e;
  --red:#d32f2f;
}
*{margin:0;padding:0;box-sizing:border-box}
html,body{width:1200px;height:3557px;overflow:hidden}
body{position:relative;font-family:'Montserrat',sans-serif;color:var(--ink);background:var(--paper)}
.abs{position:absolute}

/* top bar */
.topbar{left:0;top:0;width:1200px;height:47px;background:var(--paper);font-size:13px;font-weight:500}
.topbar .address{left:92px;top:15px;display:flex;align-items:center;gap:10px}
.topbar .phone{right:92px;top:13px;font-size:17px;font-weight:600;display:flex;align-items:center;gap:12px}

/* nav */
.nav{left:0;top:47px;width:1200px;height:91px;background:var(--night)}
.brand{left:92px;top:24px;display:flex;align-items:center;gap:10px;color:var(--paper)}
.brand-dot{width:34px;height:34px;border-radius:50%;background:var(--accent)}
.brand-name{font-size:22px;font-weight:500;letter-spacing:1px;line-height:1}
.brand-sub{font-size:10px;color:var(--accent);margin-top:4px}
.menu-links{right:92px;top:34px;display:flex;gap:48px;font-size:15px;color:var(--paper);list-style:none}
.menu-links .active{color:var(--accent)}

/* hero */
.hero{left:0;top:138px;width:1200px;height:622px;background:radial-gradient(ellipse at 50% 40%,#4a2e22 0%,#24160f 45%,#0e0a08 100%)}
.hero h1{left:0;width:1200px;top:195px;text-align:center;color:var(--paper);font-size:40px;font-weight:700;letter-spacing:1px}
.hero p{left:300px;width:600px;top:258px;text-align:center;color:var(--paper);font-size:22px;line-height:33px}
.btn-light{left:460px;top:349px;width:282px;height:60px;border-radius:30px;background:var(--paper);color:var(--ink);font-size:17px;font-weight:700;display:flex;align-items:center;justify-content:center}
.hero-dots{left:555px;top:465px;display:flex;gap:8px}
.hero-dots span{width:18px;height:18px;border-radius:50%;border:2px solid var(--paper)}
.hero-dots .on{background:var(--paper)}
.hero-wave{left:0;top:520px}

/* about */
.about h2{left:92px;top:882px;font-size:33px;font-weight:700;line-height:48px;width:520px}
.about p{left:92px;top:1035px;width:470px;font-size:17px;font-weight:500;line-height:41px}
.btn-accent{background:var(--accent);color:var(--paper);font-weight:700;display:flex;align-items:center;justify-content:center;border-radius:34px}
.about .btn-accent{left:92px;top:1238px;width:185px;height:65px;font-size:17px}
.about-frame{left:624px;top:911px;width:519px;height:386px;border:4px solid var(--ink)}
.about-photo{left:602px;top:885px;width:510px;height:379px;background:linear-gradient(135deg,#5a3a24,#2a1a10 55%,#7a5030)}

/* welcome band */
.band-photo{left:0;top:1426px;width:605px;height:455px;background:linear-gradient(120deg,#7d6a55,#3d3229 50%,#a08d74)}
.band-panel{left:605px;top:1426px;width:595px;height:455px;background:var(--grey)}
.welcome-box{left:655px;top:1456px;width:493px;height:389px;border:4px solid var(--accent);text-align:center}
.flag{left:220px;top:22px;width:46px;height:38px}
.welcome-box .w1{top:84px;left:0;width:100%;font-size:21px;font-weight:600}
.welcome-box .w2{top:116px;left:0;width:100%;font-size:33px;font-weight:800;color:var(--accent);letter-spacing:1px}
.welcome-box .w3{top:164px;left:0;width:100%;font-size:21px;font-weight:500}
.welcome-box .w4{top:196px;left:0;width:100%;font-size:16px;font-weight:700;color:var(--red)}
.welcome-box .w5{top:230px;left:0;width:100%;font-size:22px;line-height:35px}
.welcome-box .btn-accent{left:147px;top:305px;width:205px;height:53px;font-size:15px}

/* menu */
.menu-title{left:89px;top:1982px;font-size:33px;font-weight:700;color:var(--accent)}
.menu-cats{left:92px;top:2072px;list-style:none;font-size:18px;line-height:59.5px}
.menu-cats .active{color:var(--accent)}
.dish{top:2000px;width:334px;height:403px}
.dish-1{left:420px;background:linear-gradient(160deg,#7a5a3a,#b57a2c 45%,#4a3020)}
.dish-2{left:776px;background:linear-gradient(160deg,#2a1a12,#8a3a16 45%,#3a2418)}
.menu-dots{left:424px;top:2455px;display:flex;gap:7px}
.menu-dots span{width:19px;height:19px;border-radius:50%;border:2px solid var(--accent)}
.menu-dots .on{background:var(--accent)}

/* contact */
.contact-bg{left:0;top:2550px;width:1200px;height:600px}
.contact h2{left:92px;top:2674px;font-size:33px;font-weight:700}
.field{background:var(--paper);border:1px solid var(--line);border-radius:4px;padding:0 22px;font-size:16px;color:var(--muted);display:flex;align-items:center}
.field-name{left:92px;top:2747px;width:477px;height:66px}
.field-email{left:92px;top:2830px;width:477px;height:66px}
.field-phone{left:92px;top:2915px;width:477px;height:66px}
.field-question{left:590px;top:2747px;width:477px;height:149px;align-items:flex-start;padding-top:22px}
.btn-submit{left:590px;top:2915px;width:171px;height:64px;background:var(--ink);color:var(--paper);font-size:20px;font-weight:800;display:flex;align-items:center;justify-content:center;border-radius:3px}

/* footer */
.footer{left:0;top:3150px;width:1200px;height:407px;background:var(--night);color:var(--paper)}
.footer h3{font-size:24px;font-weight:700;letter-spacing:.5px}
.footer ul{list-style:none;font-size:14px;font-weight:500;line-height:25.5px;margin-top:18px}
.col-links{left:92px;top:94px}
.col-menu{left:342px;top:94px}
.footer .btn-res{left:555px;top:124px;width:254px;height:52px;background:var(--accent);color:var(--paper);font-size:14px;font-weight:700;display:flex;align-items:center;justify-content:center}
.follow{left:555px;width:254px;top:206px;text-align:center;font-size:17px;font-weight:500}
.social{left:647px;top:256px;display:flex;gap:28px}
.social span{width:14px;height:14px;border-radius:50%;background:var(--paper)}
.col-contact{left:927px;top:94px}
.col-contact .item{display:flex;gap:16px;font-size:14px;font-weight:500;line-height:25px;margin-top:18px}
.footer-rule{left:92px;top:348px;width:1016px;height:1px;background:#2a2a2a}
.copyright{left:0;width:1200px;top:367px;text-align:center;font-size:13px;font-weight:500}
</style>
</head>
<body>

<header>
  <div class="abs topbar">
    <div class="abs address">
      <svg width="14" height="18" viewBox="0 0 14 18"><path d="M7 1a5.5 5.5 0 0 0-5.5 5.5C1.5 11 7 17 7 17s5.5-6 5.5-10.5A5.5 5.5 0 0 0 7 1z" fill="none" stroke="#b23a5a" stroke-width="1.6"/><circle cx="7" cy="6.5" r="2" fill="#b23a5a"/></svg>
      <span>Teatro Lucerna, Keizerslaan 42, 1016AB Amsterdam</span>
    </div>
    <div class="abs phone">
      <svg width="18" height="18" viewBox="0 0 24 24"><path d="M6.6 10.8a15 15 0 0 0 6.6 6.6l2.2-2.2a1 1 0 0 1 1-.25 11.4 11.4 0 0 0 3.6.57 1 1 0 0 1 1 1V20a1 1 0 0 1-1 1A17 17 0 0 1 3 4a1 1 0 0 1 1-1h3.5a1 1 0 0 1 1 1c0 1.25.2 2.45.57 3.57a1 1 0 0 1-.25 1z" fill="#b23a5a"/></svg>
      <span>(+31) 20 555 0182</span>
    </div>
  </div>

  <nav class="abs nav">
    <div class="abs brand">
      <span class="brand-dot"></span>
      <div>
        <div class="brand-name">TEATRO LUCERNA</div>
        <div class="brand-sub">Ristorante Italiano</div>
      </div>
    </div>
    <ul class="abs menu-links">
      <li class="active">Home</li><li>Menu</li><li>Group Menu</li><li>Reservation</li><li>Contact</li>
    </ul>
  </nav>

  <section class="abs hero" role="img" aria-label="Photo of a candlelit restaurant dining room with wine glasses">
    <h1 class="abs">AUTHENTIC ITALIAN KITCHEN</h1>
    <p class="abs">Sed ut perspiciatis unde omnis iste natus error sit voluptatem accusantium doloremque</p>
    <div class="abs btn-light">BOOK RESERVATION</div>
    <div class="abs hero-dots"><span class="on"></span><span></span><span class="on"></span></div>
    <svg class="abs hero-wave" width="1200" height="102" viewBox="0 0 1200 102" preserveAspectRatio="none">
      <path d="M0 58 C120 40 220 72 340 60 C470 46 560 20 700 24 C840 28 960 50 1080 44 C1130 42 1170 46 1200 42 L1200 102 L0 102 Z" fill="#ffffff"/>
      <path d="M0 58 C120 40 220 72 340 60 C470 46 560 20 700 24 C840 28 960 50 1080 44 C1130 42 1170 46 1200 42" fill="none" stroke="#ffffff" stroke-width="6" stroke-opacity=".6"/>
    </svg>
  </section>
</header>

<main>
  <section class="about">
    <h2 class="abs">WE CREATED BEST DINNING EXPERIENCE FOR YOU &amp; YOUR FAMILY</h2>
    <p class="abs">Morbi leo risus, porta ac consectetur ac, vesti bulum at eros. Aenean lacinia bibendum nulla sed consec us eget urna mollis ornare vel euleo. Nullam id dolor id nibh</p>
    <div class="abs btn-accent">READ MORE</div>
    <div class="abs about-frame"></div>
    <div class="abs about-photo" role="img" aria-label="Photo of friends sharing dinner at a restaurant table"></div>
  </section>

  <section class="welcome">
    <div class="abs band-photo" role="img" aria-label="Photo of guests chatting over coffee on a café terrace"></div>
    <div class="abs band-panel"></div>
    <div class="abs welcome-box">
      <svg class="abs flag" viewBox="0 0 46 38"><path d="M2 8 Q10 2 16 6 L16 34 Q10 30 2 36 Z" fill="#2e8b3e"/><path d="M16 6 Q23 10 30 6 L30 34 Q23 38 16 34 Z" fill="#ffffff" stroke="#ddd"/><path d="M30 6 Q37 2 44 6 L44 34 Q37 30 30 34 Z" fill="#d32f2f"/></svg>
      <div class="abs w1">WELCOME TO</div>
      <div class="abs w2">TEATRO LUCERNA</div>
      <div class="abs w3">Italian restaurant</div>
      <div class="abs w4">NOW ALSO OPEN ON SUNDAYS!</div>
      <div class="abs w5">Tue - Sat: 18:00 - 23:00<br>Sun &amp; Mon: Closed</div>
      <div class="abs btn-accent">RESERVE A TABLE</div>
    </div>
  </section>

  <section class="menu-section">
    <h2 class="abs menu-title">MENU</h2>
    <ul class="abs menu-cats">
      <li>ALL</li><li class="active">STARTERS</li><li>MAIN</li><li>DESSERT</li><li>DAILY MENU</li><li>OFFERS</li>
    </ul>
    <div class="abs dish dish-1" role="img" aria-label="Photo of fried calamari with salad in a bowl"></div>
    <div class="abs dish dish-2" role="img" aria-label="Photo of glazed fried chicken bites with onion"></div>
    <div class="abs menu-dots"><span class="on"></span><span></span><span class="on"></span></div>
  </section>

  <section class="contact">
    <svg class="abs contact-bg" width="1200" height="600" viewBox="0 0 1200 600" preserveAspectRatio="none">
      <path d="M0 20 C80 8 140 30 220 22 C320 12 420 34 520 26 C640 16 760 30 880 22 C980 14 1080 30 1200 18 L1200 548 C1100 560 980 536 860 548 C740 560 620 538 500 550 C380 562 240 540 120 552 C70 556 30 550 0 552 Z" fill="#ececec"/>
      <path d="M0 552 C30 550 70 556 120 552 C240 540 380 562 500 550 C620 538 740 560 860 548 C980 536 1100 560 1200 548 L1200 600 L0 600 Z" fill="#0b0b0b"/>
    </svg>
    <h2 class="abs">CONTACT US</h2>
    <div class="abs field field-name">Name</div>
    <div class="abs field field-email">Email</div>
    <div class="abs field field-phone">Phone Number</div>
    <div class="abs field field-question">Question</div>
    <div class="abs btn-submit">SUBMIT</div>
  </section>
</main>

<footer class="abs footer">
  <div class="abs col-links">
    <h3>LINKS</h3>
    <ul><li>Home</li><li>Menu</li><li>Group Menu</li><li>Reservation</li><li>Contact</li></ul>
  </div>
  <div class="abs col-menu">
    <h3>MENU</h3>
    <ul><li>All</li><li>Starters</li><li>Main</li><li>Dessert</li><li>Daily Menu</li><li>Offers</li></ul>
  </div>
  <div class="abs btn-res">ONLINE RESERVATION</div>
  <div class="abs follow">FOLLOW</div>
  <div class="abs social"><span></span><span></span></div>
  <div class="abs col-contact">
    <h3>CONTACT</h3>
    <div class="item">
      <svg width="14" height="18" viewBox="0 0 14 18"><path d="M7 1a5.5 5.5 0 0 0-5.5 5.5C1.5 11 7 17 7 17s5.5-6 5.5-10.5A5.5 5.5 0 0 0 7 1z" fill="none" stroke="#b23a5a" stroke-width="1.6"/><circle cx="7" cy="6.5" r="2" fill="#b23a5a"/></svg>
      <div>Teatro Lucerna<br>Keizerslaan 42<br>1016AB Amsterdam</div>
    </div>
    <div class="item">
      <svg width="16" height="16" viewBox="0 0 24 24"><path d="M6.6 10.8a15 15 0 0 0 6.6 6.6l2.2-2.2a1 1 0 0 1 1-.25 11.4 11.4 0 0 0 3.6.57 1 1 0 0 1 1 1V20a1 1 0 0 1-1 1A17 17 0 0 1 3 4a1 1 0 0 1 1-1h3.5a1 1 0 0 1 1 1c0 1.25.2 2.45.57 3.57a1 1 0 0 1-.25 1z" fill="#b23a5a"/></svg>
      <div>(+31) 20 555 0182</div>
    </div>
  </div>
  <div class="abs footer-rule"></div>
  <div class="abs copyright">© 2018 Teatro Lucerna | All Rights Reserved</div>
</footer>

</body>
</html>
```